Business Card Design

Business Card for professional consulting firm working with large financial institutions.

Target Market(s)

Executive buyers

Industry/Entity Type

Banking

Contact Information for Business Card

Mild creativity wanted. Not boring, but do elaborate artwork.

Font styles to use
Serif
Sans Serif

Colors

Designer to choose colors to be used in the design.

Requirements
Must have
• Standard business card features - company name, individual name, telephone, website, email, locations.
Nice to have
• Two colors
Should not have
• too many colors, fancy printing, cartoons.

```html
<!DOCTYPE html>
<html lang="en">
<head>
<meta charset="utf-8">
<title>Business Card – Front and Back</title>
<link href="https://fonts.googleapis.com/css2?family=Roboto:wght@400;500&family=Roboto+Condensed:wght@500&display=swap" rel="stylesheet">
<style>
  :root {
    --backdrop: #e4e4e4;
    --card-front: #f4f4f4;
    --card-back: #a6a6a6;
    --ink: #1a1a1a;
    --ink-soft: #3a3a3a;
    --muted: #8a8a8a;
    --rule: #8c8c8c;
    --stripe-dark: #0d0d0d;
    --stripe-light: #a4a4a4;
    --url-ink: #505050;
  }
  * { margin: 0; padding: 0; box-sizing: border-box; }
  html, body {
    width: 1200px; height: 960px; overflow: hidden;
    background: var(--backdrop);
    font-family: "Roboto", Arial, sans-serif;
  }
  .canvas { position: relative; width: 1200px; height: 960px; }

  .card {
    position: absolute; width: 601px; height: 343px;
    box-shadow: 1px 2px 3px rgba(0,0,0,0.35);
  }
  .card--front { left: 314px; top: 113px; background: var(--card-front); }
  .card--back  { left: 311px; top: 472px; background: var(--card-back); }

  .side-stripe { position: absolute; left: 0; top: 0; width: 24px; height: 343px; }

  .wordmark {
    position: absolute; font-family: "Roboto", Arial, sans-serif;
    font-weight: 400; color: var(--ink); white-space: nowrap;
    display: flex; align-items: center; gap: 10px;
  }
  .wordmark__dot {
    display: inline-block; border-radius: 50%; background: var(--ink);
  }
  .card--front .wordmark { right: 52px; top: 54px; font-size: 28px; letter-spacing: 0.3px; }
  .card--front .wordmark__dot { width: 12px; height: 12px; }
  .card--back .wordmark { left: 0; right: 0; justify-content: center; top: 142px; font-size: 34px; }
  .card--back .wordmark__dot { width: 14px; height: 14px; }

  .person { position: absolute; left: 62px; top: 184px; }
  .person__name {
    font-family: "Roboto Condensed", "Arial Narrow", sans-serif;
    font-weight: 500; font-size: 23px; color: var(--ink); letter-spacing: 0.2px;
  }
  .person__title { font-size: 14.5px; color: var(--muted); margin-top: 1px; }

  .divider {
    position: absolute; left: 62px; top: 237px; width: 495px;
    height: 1px; background: var(--rule);
  }

  .contact-list { position: absolute; left: 62px; top: 251px; list-style: none; }
  .contact-list li {
    display: flex; align-items: center; gap: 8px;
    font-size: 14px; line-height: 19px; color: var(--ink-soft);
  }
  .contact-list svg { width: 13px; height: 13px; fill: var(--ink); flex: none; }

  .address {
    position: absolute; right: 42px; top: 251px; text-align: right;
    font-style: normal; font-size: 14px; line-height: 19px; color: var(--ink-soft);
  }

  .back-url {
    position: absolute; left: 0; right: 0; top: 281px; text-align: center;
    font-size: 14px; letter-spacing: 5px; color: var(--url-ink);
  }
</style>
</head>
<body>
<main class="canvas">

  <section class="card card--front" aria-label="Business card front">
    <svg class="side-stripe" viewBox="0 0 24 343" aria-hidden="true">
      <polygon points="0,0 24,0 24,106 0,86" fill="var(--stripe-light)"/>
      <polygon points="0,92 24,112 24,343 0,343" fill="var(--stripe-dark)"/>
    </svg>

    <div class="wordmark"><span class="wordmark__dot"></span>northledger</div>

    <div class="person">
      <h1 class="person__name">DANIEL REYES</h1>
      <p class="person__title">CEO/FOUNDER</p>
    </div>

    <div class="divider"></div>

    <ul class="contact-list">
      <li>
        <svg viewBox="0 0 24 24"><path d="M6.6 10.8a15.1 15.1 0 0 0 6.6 6.6l2.2-2.2a1 1 0 0 1 1-.25 11.4 11.4 0 0 0 3.6.57 1 1 0 0 1 1 1V20a1 1 0 0 1-1 1A17 17 0 0 1 3 4a1 1 0 0 1 1-1h3.5a1 1 0 0 1 1 1c0 1.25.2 2.45.57 3.57a1 1 0 0 1-.25 1z"/></svg>
        555 014 2286
      </li>
      <li>
        <svg viewBox="0 0 24 24"><path d="M2 5h20v14H2z M4 7v1l8 5 8-5V7l-8 5z" fill-rule="evenodd"/></svg>
        info@northledger.com
      </li>
      <li>
        <svg viewBox="0 0 24 24"><path d="M12 2a10 10 0 1 0 0 20 10 10 0 0 0 0-20zm-1 17.9A8 8 0 0 1 4.2 10.5L9 15.3v1a2 2 0 0 0 2 2zm6.9-2.5A2 2 0 0 0 16 16h-1v-3a1 1 0 0 0-1-1H8v-2h2a1 1 0 0 0 1-1V7h2a2 2 0 0 0 2-2v-.4a8 8 0 0 1 2.9 12.8z"/></svg>
        www.northledger.com
      </li>
    </ul>

    <address class="address">
      northledger<br>
      1420 Cedar Hollow Road<br>
      Juneau, Alaska 99801
    </address>
  </section>

  <section class="card card--back" aria-label="Business card back">
    <div class="wordmark"><span class="wordmark__dot"></span>northledger</div>
    <p class="back-url">www.northledger.com</p>
  </section>

</main>
</body>
</html>
```